Research and Innovation programme/projects in WOOD based industries

1.Pramenova s.r.o. (offical registered brand name of our company)
-Managing technology development projects
-International cooperation and development European projects
Our company was founded in 2008 and started to work as a counsilary company operating in the section of european funds administrated by Czech republic. Nowadays we are specializing on projects in the sphere of science and research co-financed by EU.Since 6.6.2013 we are registered under European comission for a purpose of broad support of transnational projects.

Target Market(s)

We are primarily focused on european companies, which stand behind the latest research and innovation of sawing, planing, glulam and logging technologies based on wooden materials.

Coding

Coded - Design and coding required

Number of Pages Required

5+ page

Font styles to use
Serif

Colors
cadf82
abd037
9bcb3c
fee18a
ffcf3e
ffc214

Requirements
Must have
• The web will exist in three possible languages in czech, english and deutsch.
• First page : introduction of a company
• Second page : Area of expertise
• Third page: servicies our company provides
• Fourth page: Our partners
• Fifth page: Conditions of our servicies
• Sixth page: Succesful projects
• - we would also love if we had possibility to add videos about our successful projects
• Seventh: Our team
• We are serious company in the sphere of funds and counsilary servicies, that is why we would love to have web design as representative as possible
• Take on mind that that we are specializing on development management, try to apply that on your design
• In the section of contacts, we would love to have photos of our team,
• This is our current site: http://www.pramenova-example.eu/cz/partneri.html
• This is how our concurency sites are lookin. Take these designs as an slight inspiration.
• http://www.lumatrava-example.sk/en/
• https://www2.brenvick-example.com/global/en.html
Nice to have
• Visible logo on the front page for the visitor.
• As a inspiration we provided link for our current web design, but we dont want to copy the current style, just look at the logo and the pages that exists on current web.
• !!!!!!We also uploaded file, where we explain how our cooperation with partner works. Especially in the part 2. section of service. Take that as an ispiration too, or use that to understand, what our company do.
Should not have
• We are serious company in the sphere of funds and counsilary servicies, that is why we would love to have web design representative as possible

```html
<!DOCTYPE html>
<html lang="en">
<head>
<meta charset="utf-8">
<title>1. Pramenova s.r.o. – Research and Innovation in Wood Based Industries</title>
<link href="https://fonts.googleapis.com/css2?family=Lato:wght@400;700;900&family=Merriweather+Sans:wght@400;700&display=swap" rel="stylesheet">
<style>
:root{
  --green:#9bcb3c;
  --green-mid:#abd037;
  --green-tile:#b7d96b;
  --yellow:#ffc214;
  --yellow-soft:#fee18a;
  --ink:#333333;
  --text:#555555;
  --grey-bg:#f2f2f2;
  --footer-bar:#3a3a3a;
  --white:#ffffff;
}
*{margin:0;padding:0;box-sizing:border-box}
html,body{width:1200px;height:5329px;overflow:hidden}
body{font-family:'Lato',sans-serif;color:var(--text);background:var(--white);position:relative}
.abs{position:absolute}
.btn{position:absolute;background:var(--yellow);color:var(--white);font-weight:700;font-size:13px;text-transform:uppercase;display:flex;align-items:center;justify-content:center;letter-spacing:.3px}
.section-title{position:absolute;left:0;width:1200px;text-align:center;font-size:27px;font-weight:700;color:var(--ink);text-transform:uppercase}

/* header */
.site-header{position:absolute;top:0;left:0;width:1200px;height:95px;background:var(--white)}
.brand{position:absolute;left:75px;top:33px;display:flex;align-items:center;gap:14px}
.brand-mark{width:52px;height:32px;background:var(--green)}
.brand-name{font-size:16px;font-weight:700;color:var(--ink);line-height:1.1}
.brand-name small{display:block;font-size:12px;font-weight:700;color:var(--text)}
.call{position:absolute;left:818px;top:28px;display:flex;align-items:center;gap:10px}
.call-icon{width:30px;height:30px;border-radius:50%;background:var(--yellow);display:flex;align-items:center;justify-content:center}
.call-label{font-size:10px;color:var(--yellow);font-weight:700}
.call-number{font-size:20px;font-weight:700;color:var(--ink);line-height:1}
.lang{position:absolute;left:1065px;top:38px;font-size:11px;display:flex;gap:6px;align-items:center;color:var(--ink)}
.lang i{width:18px;height:11px;background:#2b3f8a;display:block}
.main-nav{position:absolute;top:95px;left:0;width:1200px;height:54px;background:var(--green);display:flex;justify-content:center;align-items:center;gap:46px}
.main-nav a{color:var(--white);font-size:13px;font-weight:700;text-decoration:none;text-transform:uppercase}

/* hero */
.hero{position:absolute;top:149px;left:0;width:1200px;height:575px;background:linear-gradient(180deg,#5d5c55 0%,#7b766b 45%,#4b4a44 100%)}
.hero-title{position:absolute;top:185px;width:1200px;text-align:center;color:var(--white);font-family:'Merriweather Sans',sans-serif;font-weight:700;font-size:52px;letter-spacing:1px}
.hero-sub{position:absolute;top:250px;width:1200px;text-align:center;color:var(--white);font-family:'Merriweather Sans',sans-serif;font-size:27px;line-height:34px}
.dots{position:absolute;top:540px;left:563px;display:flex;gap:13px}
.dots span{width:10px;height:10px;border-radius:50%;background:var(--white)}
.dots span:first-child{background:var(--green)}

/* about */
.about-text{position:absolute;left:105px;width:990px;text-align:center;font-size:13.5px;line-height:28px}

/* services */
.services-bg{position:absolute;top:1097px;left:0}
.tile{position:absolute;width:340px;height:160px;background:var(--green-tile);color:var(--white);display:flex;flex-direction:column;align-items:center;justify-content:flex-end;padding-bottom:22px;text-align:center;font-size:19px;line-height:24px;text-transform:uppercase}
.tile svg{margin-bottom:14px}

/* expertise */
.exp-card{position:absolute;top:1905px;width:330px;height:273px;background:var(--grey-bg);text-align:center;padding:0 18px}
.exp-icon{width:100px;height:80px;margin:26px auto 18px;background:var(--yellow);border-radius:10px}
.exp-card h3{color:var(--green);font-size:17px;font-weight:700;text-transform:uppercase;margin-bottom:6px}
.exp-card p{font-size:13.5px;line-height:25px}

/* partners */
.partner{position:absolute;top:2422px;width:278px;height:105px;background:var(--white);display:flex;align-items:center;justify-content:center}
.partner span{width:170px;height:46px;background:#d9d9d9;border-radius:4px}

/* conditions */
.cond-title{position:absolute;left:75px;top:2711px;font-size:28px;font-weight:700;color:var(--ink);text-transform:uppercase}
.cond-text{position:absolute;left:75px;top:2760px;width:515px;font-size:13.5px;line-height:28px}
.photo{position:absolute}

/* projects */
.video{position:absolute;width:512px;height:248px}
.play{position:absolute;left:236px;top:104px;width:40px;height:40px;border-radius:50%;background:var(--white);display:flex;align-items:center;justify-content:center}

/* team */
.member{position:absolute;top:4037px;width:238px;text-align:center}
.member .portrait{width:238px;height:218px;border:1px solid #ccc}
.member h4{margin-top:32px;color:var(--green);font-size:14px;font-weight:700;text-transform:uppercase}
.member p{font-size:13.5px;line-height:25px;margin-top:6px;padding:0 10px}
.member a{display:block;margin-top:8px;color:var(--yellow);font-size:13.5px}

/* contact */
.contact-panel{position:absolute;top:4469px;left:587px;width:613px;height:466px;background:var(--green);color:var(--white)}
.contact-panel h2{position:absolute;left:27px;top:48px;font-size:28px;font-weight:700}
.contact-line{position:absolute;left:27px;font-size:15px;display:flex;align-items:center;gap:10px}
.field{position:absolute;background:var(--white);color:var(--ink);font-size:10.5px;font-weight:700;padding:15px 14px;text-transform:uppercase}

/* footer */
.foot-col{position:absolute;top:4980px}
.foot-col h5{font-size:17px;font-weight:700;color:var(--ink);text-transform:uppercase;margin-bottom:14px}
.foot-col li{list-style:none;font-size:13.5px;line-height:32.5px;color:var(--text)}
.foot-bar{position:absolute;top:5255px;left:0;width:1200px;height:74px;background:var(--footer-bar);color:#ddd;font-size:11px}
.foot-bar p{position:absolute;left:75px;top:30px}
.social{position:absolute;left:940px;top:24px;display:flex;gap:21px}
.social span{width:20px;height:20px;border-radius:50%;background:#9a9a9a}
</style>
</head>
<body>

<header class="site-header">
  <div class="brand">
    <div class="brand-mark"></div>
    <div class="brand-name">1. PRAMENOVA S.R.O.<small>Beratungsfirma</small></div>
  </div>
  <div class="call">
    <div class="call-icon"><svg width="14" height="14" viewBox="0 0 24 24"><path fill="#fff" d="M6.6 10.8a15 15 0 006.6 6.6l2.2-2.2a1 1 0 011-.25 11.4 11.4 0 003.6.6 1 1 0 011 1V20a1 1 0 01-1 1A17 17 0 013 4a1 1 0 011-1h3.5a1 1 0 011 1c0 1.25.2 2.45.6 3.6a1 1 0 01-.25 1z"/></svg></div>
    <div><div class="call-label">CALL US</div><div class="call-number">1-800-555-0142</div></div>
  </div>
  <div class="lang"><i></i>EN ⌄</div>
</header>

<nav class="main-nav">
  <a>Home</a><a>Area of Expertise</a><a>Services</a><a>Partners</a><a>Projects</a><a>Our Team</a><a>Contact Us</a>
</nav>

<section class="hero" role="img" aria-label="Photo of a sawmill workshop with timber on a conveyor line">
  <h1 class="hero-title">PRAMENOVA</h1>
  <p class="hero-sub">We provide Research and Innovation<br>programme/projects in WOOD based industries.</p>
  <div class="btn" style="left:517px;top:338px;width:166px;height:44px">Read More</div>
  <div class="dots"><span></span><span></span><span></span><span></span></div>
</section>

<section class="about">
  <h2 class="section-title" style="top:778px">About Our Company</h2>
  <p class="about-text" style="top:824px">Donec sit amet tortor eu tellus ultricies tempus sed quis augue. Praesent quis metus non est tristique ornare ac vel arcu. Nulla 16iaculis libero et erat tempus venenatis. Aliquam sed finibus odio. Quisque euismod mi id enim imperdiet tincidunt. Nullam commodo est vitae pharetra ultrices. Phasellus sagittis blandit mi feugiat fermentum. Aliquam commodo, dolor vel finibus commodo, lacus lorem aliquet est..</p>
  <p class="about-text" style="top:920px">Phasellus sagittis blandit mi feugiat fermentum. Ut arcu libero, rhoncus vel semper sed, venenatis sit amet lectus. In euismod magna et eros accumsan tempus. Aliquam commodo, dolor vel finibus commodo, lacus lorem aliquet est..</p>
  <div class="btn" style="left:517px;top:1012px;width:166px;height:45px">Read More</div>
</section>

<section class="services">
  <svg class="services-bg" width="1200" height="693" viewBox="0 0 1200 693">
    <path fill="#9bcb3c" d="M0 0 Q600 110 1200 10 L1200 620 Q600 640 0 693 Z"/>
  </svg>
  <h2 class="section-title" style="top:1200px;color:#fff">Services Our Company Provides</h2>
  <div class="tile" style="left:75px;top:1268px"><svg width="46" height="46" viewBox="0 0 24 24"><circle cx="12" cy="12" r="9" fill="none" stroke="#fff" stroke-width="2"/><circle cx="12" cy="12" r="3" fill="#fff"/></svg>Project<br>Coordination</div>
  <div class="tile" style="left:431px;top:1268px"><svg width="46" height="46" viewBox="0 0 24 24"><text x="12" y="20" font-size="22" font-weight="700" fill="#fff" text-anchor="middle" font-family="Lato,sans-serif">$</text></svg>Project<br>Financing</div>
  <div class="tile" style="left:787px;top:1268px"><svg width="46" height="46" viewBox="0 0 24 24"><circle cx="12" cy="10" r="5" fill="#fff"/><rect x="10" y="16" width="4" height="4" fill="#fff"/></svg>Technology &amp; Foreign<br>Trade Projects</div>
  <div class="tile" style="left:75px;top:1442px"><svg width="46" height="46" viewBox="0 0 24 24"><circle cx="12" cy="12" r="10" fill="#fff"/></svg>International<br>Development Projects</div>
  <div class="tile" style="left:431px;top:1442px"><svg width="46" height="46" viewBox="0 0 24 24"><path fill="#fff" d="M5 2h10l5 5v15H5z"/><path stroke="#b7d96b" stroke-width="1.5" d="M8 12h9M8 15h9M8 18h9"/></svg>EU<br>Projects</div>
  <div class="tile" style="left:787px;top:1442px"><svg width="46" height="46" viewBox="0 0 24 24"><path fill="none" stroke="#fff" stroke-width="3" d="M4 11a8 8 0 0114-5M20 13a8 8 0 01-14 5"/><path fill="#fff" d="M19 2v7h-7zM5 22v-7h7z"/></svg>Export<br>Promotion</div>
  <div class="btn" style="left:496px;top:1637px;width:208px;height:46px">View All Services</div>
</section>

<section class="expertise">
  <h2 class="section-title" style="top:1826px">Area of Expertise</h2>
  <div class="exp-card" style="left:75px"><div class="exp-icon"></div><h3>Aliquam sed finibus</h3><p>Donec sit amet tortor eu tellus ultricies tempus sed quis auguep raesent quis metus non est tristique ornare ac..</p></div>
  <div class="exp-card" style="left:436px"><div class="exp-icon"></div><h3>Aliquam sed finibus</h3><p>Donec sit amet tortor eu tellus ultricies tempus sed quis auguep raesent quis metus non est tristique ornare ac..</p></div>
  <div class="exp-card" style="left:797px"><div class="exp-icon"></div><h3>Aliquam sed finibus</h3><p>Donec sit amet tortor eu tellus ultricies tempus sed quis auguep raesent quis metus non est tristique ornare ac..</p></div>
</section>

<section class="partners">
  <svg class="abs" style="top:2255px;left:0" width="1200" height="404" viewBox="0 0 1200 404">
    <path fill="#fee18a" d="M0 0 Q600 60 1200 0 L1200 320 Q600 340 0 404 Z"/>
  </svg>
  <h2 class="section-title" style="top:2355px">Our Partners</h2>
  <div class="partner" style="left:164px"><span></span></div>
  <div class="partner" style="left:461px"><span></span></div>
  <div class="partner" style="left:759px"><span></span></div>
</section>

<section class="conditions">
  <h2 class="cond-title">Conditions of Our Services</h2>
  <p class="cond-text">Donec sit amet tortor eu tellus ultricies tempus sed quis augue. Praesent quis metus non est tristique ornare ac vel arcu. Nulla 16iaculis libero et erat tempus venenatis. Aliquam sed finibus odio. Quisque euismod mi id enim imperdiet tincidunt. Nullam commodo est vitae pharetra ultrices. Phasellus sagittis blandit mi feugiat fermentum. Aliquam commodo, dolor vel finibus commodo, lacus lorem aliquet est..</p>
  <div class="btn" style="left:75px;top:2945px;width:166px;height:45px">Read More</div>
  <div class="photo" style="left:615px;top:2716px;width:512px;height:276px;background:linear-gradient(160deg,#c9d2d6,#a7a195)" role="img" aria-label="Photo of a bright furniture production hall with wood panels"></div>
</section>

<section class="projects">
  <svg class="abs" style="top:3045px;left:0" width="1200" height="900" viewBox="0 0 1200 900">
    <path fill="#f2f2f2" d="M0 20 Q600 -20 1200 30 L1200 880 Q600 840 0 900 Z"/>
  </svg>
  <h2 class="section-title" style="top:3148px">Successful Projects</h2>
  <div class="video" style="left:75px;top:3219px;background:linear-gradient(150deg,#7d8a5d,#a88a62)" role="img" aria-label="Video still of a log loader stacking timber in a forest"><div class="play"><svg width="14" height="14" viewBox="0 0 10 10"><path d="M2 1l7 4-7 4z" fill="#555"/></svg></div></div>
  <div class="video" style="left:615px;top:3219px;background:linear-gradient(150deg,#8a8078,#c9b597)" role="img" aria-label="Video still of a panel processing line in a factory"><div class="play"><svg width="14" height="14" viewBox="0 0 10 10"><path d="M2 1l7 4-7 4z" fill="#555"/></svg></div></div>
  <div class="video" style="left:75px;top:3492px;background:linear-gradient(150deg,#8b7d6c,#c4b3a0)" role="img" aria-label="Video still of a carpenter working at a workbench"><div class="play"><svg width="14" height="14" viewBox="0 0 10 10"><path d="M2 1l7 4-7 4z" fill="#555"/></svg></div></div>
  <div class="video" style="left:615px;top:3492px;background:linear-gradient(150deg,#6f7a6b,#c9b08a)" role="img" aria-label="Video still of workers handling a wood panel on a machine"><div class="play"><svg width="14" height="14" viewBox="0 0 10 10"><path d="M2 1l7 4-7 4z" fill="#555"/></svg></div></div>
  <div class="btn" style="left:496px;top:3782px;width:208px;height:46px">View All Projects</div>
</section>

<section class="team">
  <h2 class="section-title" style="top:3970px">Our Team</h2>
  <div class="member" style="left:342px">
    <div class="portrait" style="background:linear-gradient(160deg,#6f665b,#a39481)" role="img" aria-label="Portrait photo of team member Karel Dvorsky"></div>
    <h4>Karel Dvorsky</h4>
    <p>Donec sit amet tortor eu tellus ultricies tempus sed quis augu metus non est..</p>
    <a>Contact Us</a>
  </div>
  <div class="member" style="left:615px">
    <div class="portrait" style="background:linear-gradient(160deg,#e9e4df,#b07a66)" role="img" aria-label="Portrait photo of team member Lenka Sedlakova"></div>
    <h4>Mgr. Lenka Sedlakova</h4>
    <p>Donec sit amet tortor eu tellus ultricies tempus sed quis augu metus non est..</p>
    <a>Contact Us</a>
  </div>
</section>

<section class="contact">
  <div class="abs" style="top:4469px;left:0;width:587px;height:466px;background:linear-gradient(150deg,#8a8175,#4f5a66)" role="img" aria-label="Photo of the consulting team gathered around a table"></div>
  <div class="contact-panel">
    <h2>CONTACT US</h2>
    <div class="contact-line" style="top:100px"><svg width="12" height="14" viewBox="0 0 12 16"><path fill="#fff" d="M6 0a6 6 0 016 6c0 4-6 10-6 10S0 10 0 6a6 6 0 016-6zm0 4a2 2 0 100 4 2 2 0 000-4z"/></svg>&nbsp;4417 Lindenfield Lane, Ostrava, 702 00</div>
    <div class="contact-line" style="top:130px"><svg width="13" height="13" viewBox="0 0 24 24"><path fill="#fff" d="M6.6 10.8a15 15 0 006.6 6.6l2.2-2.2a1 1 0 011-.25 11.4 11.4 0 003.6.6 1 1 0 011 1V20a1 1 0 01-1 1A17 17 0 013 4a1 1 0 011-1h3.5a1 1 0 011 1c0 1.25.2 2.45.6 3.6a1 1 0 01-.25 1z"/></svg>&nbsp;1-800-555-0142 &nbsp;&nbsp;&nbsp;<svg width="15" height="11" viewBox="0 0 16 12"><rect width="16" height="12" fill="#fff"/><path d="M0 0l8 6 8-6" fill="none" stroke="#9bcb3c" stroke-width="1.5"/></svg>&nbsp;info@pramenova-example.eu</div>
    <div class="field" style="left:27px;top:175px;width:248px;height:42px">Enter Name</div>
    <div class="field" style="left:293px;top:175px;width:248px;height:42px">Enter Email Address</div>
    <div class="field" style="left:27px;top:229px;width:248px;height:42px">Phone No</div>
    <div class="field" style="left:293px;top:229px;width:248px;height:42px">Subject</div>
    <div class="field" style="left:27px;top:284px;width:514px;height:74px">Message</div>
    <div class="btn" style="left:27px;top:376px;width:208px;height:46px">Contact Us</div>
  </div>
</section>

<footer>
  <div class="foot-col" style="left:75px"><h5>Site Map</h5><ul><li>Home</li><li>Area Of Expertise</li><li>Services</li><li>Partners</li><li>Projects</li><li>Our Team</li><li>Contact Us</li></ul></div>
  <div class="foot-col" style="left:315px"><h5>Area of Expertise</h5><ul><li>Donec a semper arcu</li><li>Aenean ante metus</li><li>eugiat vel egestas</li><li>arius quis mi</li><li>Curabitur vulputate gravida</li></ul></div>
  <div class="foot-col" style="left:632px"><h5>Services</h5><ul><li>Donec a semper arcu</li><li>Aenean ante metus</li><li>eugiat vel egestas</li><li>arius quis mi</li><li>Curabitur vulputate gravida</li></ul></div>
  <div class="foot-col" style="left:906px"><h5>Resources</h5><ul><li>Donec a semper arcu</li><li>Aenean ante metus</li><li>eugiat vel egestas</li><li>arius quis mi</li><li>Curabitur vulputate gravida</li></ul></div>
  <div class="foot-bar">
    <p>Copyright © 2019. Company Name. All Right Reserved</p>
    <div class="social"><span></span><span></span><span></span><span></span><span></span></div>
  </div>
</footer>

</body>
</html>
```